Business card for medical clinic

I need an upmarket, modern medical/health business card for my clinic

Contact Information for Business Card

name, address, email, qr code

```html
<!DOCTYPE html>
<html lang="en">
<head>
<meta charset="utf-8">
<title>Aurelis Health Partners – Business Card</title>
<link href="https://fonts.googleapis.com/css2?family=Montserrat:wght@400;500;700&display=swap" rel="stylesheet">
<style>
  :root {
    --stage: #2b2b2d;
    --navy: #1d2a4a;
    --navy-mid: #2c4a6c;
    --sky: #2aa8df;
    --white: #ffffff;
    --ink: #141414;
    --accent: #2b9fd9;
  }
  * { box-sizing: border-box; margin: 0; padding: 0; }
  html, body { width: 1200px; height: 689px; overflow: hidden; }
  body {
    background: var(--stage);
    font-family: "Montserrat", Arial, sans-serif;
    position: relative;
  }
  .card {
    position: absolute;
    top: 190px;
    width: 540px;
    height: 309px;
    overflow: hidden;
    box-shadow: 0 18px 40px rgba(0,0,0,.45);
  }
  /* Front side */
  .card--front {
    left: 40px;
    background: linear-gradient(45deg, var(--sky) 0%, var(--navy-mid) 55%, var(--navy) 100%);
    color: var(--white);
  }
  .brand {
    position: absolute;
    display: flex;
    align-items: center;
    gap: 14px;
  }
  .brand__dot {
    flex: none;
    border-radius: 50%;
    border: 3px solid currentColor;
  }
  .brand__name {
    font-weight: 500;
    text-transform: uppercase;
    letter-spacing: .12em;
    line-height: 1.25;
  }
  .card--front .brand { left: 95px; top: 104px; }
  .card--front .brand__dot { width: 84px; height: 84px; }
  .card--front .brand__name { font-size: 24px; }
  .front-web {
    position: absolute;
    left: 0; right: 0; bottom: 26px;
    text-align: center;
    font-size: 12px;
    letter-spacing: .03em;
  }
  .front-web svg { vertical-align: -3px; margin-right: 6px; }

  /* Back side */
  .card--back {
    left: 620px;
    background: var(--white);
    color: var(--ink);
  }
  .card--back .wave { position: absolute; inset: 0; }
  .card--back .brand { left: 30px; top: 38px; color: var(--navy); }
  .card--back .brand__dot { width: 44px; height: 44px; border-width: 2px; }
  .card--back .brand__name { font-size: 13px; }
  .person {
    position: absolute;
    right: 48px;
    top: 40px;
    text-align: left;
  }
  .person__name {
    color: var(--accent);
    font-weight: 700;
    font-size: 21px;
    letter-spacing: .01em;
    white-space: nowrap;
  }
  .person__role { font-size: 13px; margin-top: 2px; }
  .person-tab {
    position: absolute;
    right: 0; top: 42px;
    width: 18px; height: 30px;
    background: var(--navy-mid);
  }
  .address {
    position: absolute;
    left: 30px; top: 108px;
    font-size: 12.5px;
    line-height: 1.35;
  }
  .contacts {
    position: absolute;
    left: 30px; top: 150px;
    list-style: none;
    font-size: 12.5px;
    line-height: 1.5;
  }
  .contacts li { display: flex; align-items: center; gap: 8px; }
  .contacts svg { flex: none; }
</style>
</head>
<body>

<section class="card card--front" aria-label="Card front">
  <div class="brand">
    <span class="brand__dot"></span>
    <span class="brand__name">Aurelis Health<br>Partners</span>
  </div>
  <p class="front-web">
    <svg width="13" height="13" viewBox="0 0 16 16" fill="none" stroke="#fff" stroke-width="1.4"><circle cx="8" cy="8" r="6.5"/><path d="M1.5 8h13M8 1.5c2.5 3 2.5 10 0 13M8 1.5c-2.5 3-2.5 10 0 13"/></svg>www.aurelis-care.net
  </p>
</section>

<section class="card card--back" aria-label="Card back">
  <svg class="wave" viewBox="0 0 540 309" preserveAspectRatio="none" aria-hidden="true">
    <defs>
      <linearGradient id="waveFill" x1="0" y1="1" x2="1" y2="0">
        <stop offset="0" stop-color="#2aa8df"/>
        <stop offset=".55" stop-color="#2d5a80"/>
        <stop offset="1" stop-color="#1d2a4a"/>
      </linearGradient>
    </defs>
    <path d="M0,262 C160,248 300,230 370,160 C420,112 470,100 540,92 L540,100 C480,108 430,122 385,170 C320,240 170,258 0,276 Z" fill="#1d2a4a"/>
    <path d="M0,292 C170,272 330,250 410,172 C450,132 490,112 540,106 L540,309 L0,309 Z" fill="url(#waveFill)"/>
  </svg>

  <div class="brand">
    <span class="brand__dot"></span>
    <span class="brand__name">Aurelis Health<br>Partners</span>
  </div>

  <div class="person">
    <p class="person__name">DANA WHITFIELD</p>
    <p class="person__role">Managing Director</p>
  </div>
  <span class="person-tab"></span>

  <p class="address">482 Harbor Lane, Ste<br>210, Fairview, TX 75069</p>

  <ul class="contacts">
    <li>
      <svg width="13" height="13" viewBox="0 0 16 16" fill="#2b9fd9"><path d="M3 2h3l1.5 3.5-2 1.3a8 8 0 0 0 3.7 3.7l1.3-2L14 10v3a1.5 1.5 0 0 1-1.5 1.5A11.5 11.5 0 0 1 1.5 3.5 1.5 1.5 0 0 1 3 2z"/></svg>
      555-014-2200
    </li>
    <li>
      <svg width="13" height="13" viewBox="0 0 16 16" fill="#2b9fd9"><path d="M1 3h14v10H1z"/><path d="M1 3l7 6 7-6" fill="none" stroke="#fff" stroke-width="1.3"/></svg>
      hello@aurelis-care.net
    </li>
    <li>
      <svg width="13" height="13" viewBox="0 0 16 16" fill="none" stroke="#2b9fd9" stroke-width="1.6"><circle cx="8" cy="8" r="6.5"/><path d="M1.5 8h13M8 1.5c2.5 3 2.5 10 0 13M8 1.5c-2.5 3-2.5 10 0 13"/></svg>
      www.aurelis-care.net
    </li>
  </ul>
</section>

</body>
</html>
```